Presentation Folder - Stagger Cut Fliers
Harborline Property Partners
Presentation Folder - Stagger Cut Fliers - Real Estate
Creative Brief
Real Estate
Corporate. Our target audience are real estate agents and brokers. This is an industry where image and perception matter, so these designs need to invoke professionalism, be creative, and invoke confidence in our services.
The presentation folder itself needs to be very simple, but again, very professional and aesthetically pleasing. At a minimum, we need our logo on the font and the company contact information on the back. The stagger cut fliers themselves need to have the ability to put information on the front and back of the flier. There are five pages for the fliers, so you can either design five unique pages or have a template that can work for all of them. You can use filler text like that in the attached document. The fliers aren't just going to be text. You can add filler images to make more appealing, such as on the consumer demand page you can leave a spot where we can put the image of a billboard.

```html
<!DOCTYPE html>
<html lang="en">
<head>
<meta charset="utf-8">
<title>Harborline Property Partners – Stagger Cut Fliers</title>
<link rel="stylesheet" href="https://fonts.googleapis.com/css2?family=Arimo:wght@400;700&display=swap">
<style>
  :root {
    --stage: #5b5b5b;
    --navy: #0d3a78;
    --blue: #1756a6;
    --blue-light: #3f86d6;
    --sky: #cfe0f3;
    --paper: #ffffff;
    --ink: #333c48;
  }
  * { box-sizing: border-box; margin: 0; padding: 0; }
  html, body { width: 1200px; height: 976px; overflow: hidden; }
  body {
    background: var(--stage);
    font-family: "Arimo", Arial, sans-serif;
    color: var(--ink);
    position: relative;
  }
  .flier {
    position: absolute;
    background: var(--paper);
    overflow: hidden;
    box-shadow: 0 3px 10px rgba(0,0,0,.45);
  }
  .flier-header {
    position: absolute; left: 0; top: 0; width: 100%; height: 48px;
    background: linear-gradient(180deg, var(--blue-light), var(--blue) 55%, var(--navy));
    border-bottom-right-radius: 60% 18px;
  }
  .flier-title {
    position: absolute; left: 14px; top: 12px;
    color: var(--paper); font-weight: 700; font-size: 20px; letter-spacing: .2px;
  }
  .tag {
    position: absolute;
    background: linear-gradient(90deg, var(--navy), var(--blue));
    color: var(--paper); font-weight: 700; font-size: 10px;
    padding: 3px 8px; width: 120px;
  }
  .copy {
    position: absolute; font-size: 8.5px; line-height: 1.35; color: var(--ink);
  }
  .copy.light { color: var(--paper); }
  .photo {
    position: absolute; border: 3px solid var(--paper);
    box-shadow: 0 1px 4px rgba(0,0,0,.3);
  }
  .swoosh { position: absolute; left: 0; bottom: 0; width: 100%; }
  .brand {
    position: absolute; display: flex; align-items: center; gap: 5px;
    font-size: 10px; font-weight: 700; color: var(--navy); white-space: nowrap;
  }
  .brand-dot { width: 12px; height: 12px; border-radius: 50%; background: var(--blue); }
  .brand.on-dark { color: var(--paper); }
  .brand.on-dark .brand-dot { background: var(--paper); }

  .features { left: 40px; top: 32px; width: 348px; height: 558px; }
  .demand   { left: 422px; top: 32px; width: 348px; height: 558px; }
  .leads    { left: 805px; top: 32px; width: 348px; height: 558px; }
  .roi      { left: 205px; top: 615px; width: 380px; height: 335px; }
  .broker   { left: 610px; top: 615px; width: 380px; height: 335px; }

  .broker-panel {
    position: absolute; left: 0; width: 100%;
    background: linear-gradient(180deg, var(--blue), var(--navy));
  }
  .broker-head {
    position: absolute; color: var(--paper); font-weight: 700; font-size: 11px;
  }
</style>
</head>
<body>

<section class="flier features">
  <div class="flier-header"><h2 class="flier-title">ScanPath Features</h2></div>
  <div class="tag" style="left:14px;top:62px">Feature 1</div>
  <p class="copy" style="left:14px;top:84px;width:320px">Scan a code and buyers see listing details, photos, pricing and agent contact at once on any phone, with no app to download and nothing to type. Every sign works around the clock for you.</p>
  <div class="tag" style="left:14px;top:134px">Feature 2</div>
  <p class="copy" style="left:14px;top:156px;width:320px">Each sign rider carries its own code, so every inquiry is tracked back to the property and the agent. You always know which listing started the conversation and where buyers came from.</p>
  <div class="tag" style="left:14px;top:206px">Feature 3</div>
  <p class="copy" style="left:14px;top:228px;width:320px">Leads arrive by text and email within seconds, ready for a quick and personal follow up. Names and numbers are saved automatically, so your team can reply while interest is still high.</p>
  <div class="tag" style="left:14px;top:278px">Feature 4</div>
  <p class="copy" style="left:14px;top:300px;width:320px">Simple reports show which listings draw the most interest and when buyers are looking. Use the numbers to plan open houses, adjust pricing and show sellers the value of your marketing.</p>
  <div role="img" aria-label="Photo of a suburban house with a for-sale sign on the lawn"
       style="position:absolute;left:180px;top:350px;width:168px;height:150px;background:linear-gradient(180deg,#d7e4ef,#9fb3c6 55%,#6f9a52)"></div>
  <svg class="swoosh" viewBox="0 0 348 90" height="90" preserveAspectRatio="none" aria-hidden="true">
    <path d="M0 40 Q170 10 348 55 L348 90 L0 90 Z" fill="#cfe0f3"/>
    <path d="M0 55 Q180 28 348 70 L348 90 L0 90 Z" fill="#1756a6"/>
    <path d="M0 70 Q190 48 348 80 L348 90 L0 90 Z" fill="#0d3a78"/>
  </svg>
  <div class="brand" style="left:14px;top:484px"><span class="brand-dot"></span>Harborline Property Partners</div>
</section>

<section class="flier demand">
  <div class="flier-header"><h2 class="flier-title">Consumer Demand</h2></div>
  <div class="tag" style="left:14px;top:62px">Technique 1</div>
  <p class="copy" style="left:14px;top:84px;width:160px">Buyers search on their phones first, so every sign becomes an instant listing.</p>
  <div class="photo" role="img" aria-label="Space for a billboard image" style="left:182px;top:58px;width:152px;height:84px;background:linear-gradient(180deg,#e7eef6,#b8cbe0)"></div>
  <div class="photo" role="img" aria-label="Photo of a studio microphone" style="left:14px;top:156px;width:96px;height:90px;background:linear-gradient(160deg,#b04a3a,#6a2a24)"></div>
  <div class="tag" style="left:120px;top:160px">Technique 2</div>
  <p class="copy" style="left:120px;top:182px;width:214px">Radio and print spots point listeners to one short code they can text.</p>
  <div class="tag" style="left:14px;top:262px">Technique 3</div>
  <p class="copy" style="left:14px;top:284px;width:160px">Open house visitors check in by phone and receive details before they leave.</p>
  <div class="photo" role="img" aria-label="Photo of an open house interior" style="left:182px;top:256px;width:152px;height:88px;background:linear-gradient(180deg,#e6dccb,#b79f80)"></div>
  <div class="photo" role="img" aria-label="Screenshot of an online listing ad" style="left:14px;top:356px;width:160px;height:84px;background:linear-gradient(180deg,#eef3f9,#a9c1dc)"></div>
  <div class="tag" style="left:184px;top:372px">Technique 4</div>
  <p class="copy" style="left:184px;top:394px;width:150px">Online ads carry the same code, keeping the message clear across every channel.</p>
  <svg class="swoosh" viewBox="0 0 348 90" height="90" preserveAspectRatio="none" aria-hidden="true">
    <path d="M0 55 Q170 20 348 40 L348 90 L0 90 Z" fill="#cfe0f3"/>
    <path d="M0 70 Q180 38 348 55 L348 90 L0 90 Z" fill="#1756a6"/>
    <path d="M0 80 Q190 55 348 68 L348 90 L0 90 Z" fill="#0d3a78"/>
  </svg>
  <div class="brand" style="right:14px;top:488px"><span class="brand-dot"></span>Harborline Property Partners</div>
</section>

<section class="flier leads">
  <div class="flier-header"><h2 class="flier-title">Lead Generation</h2></div>
  <div class="tag" style="left:14px;top:66px">Technique 1</div>
  <p class="copy" style="left:14px;top:88px;width:150px">Every scan captures a name and number so no interested buyer slips away.</p>
  <div class="photo" role="img" aria-label="Photo of a smiling family" style="left:172px;top:56px;width:162px;height:110px;background:linear-gradient(180deg,#c7d9ea,#c59a7a)"></div>
  <div class="tag" style="left:14px;top:186px">Technique 2</div>
  <p class="copy" style="left:14px;top:208px;width:150px">Agents get an alert the moment a buyer asks about a home.</p>
  <div class="photo" role="img" aria-label="Photo of a brick family home" style="left:172px;top:180px;width:162px;height:108px;background:linear-gradient(180deg,#b9d1ea,#9a6d52 60%,#6b9a4c)"></div>
  <div class="tag" style="left:14px;top:306px">Technique 3</div>
  <p class="copy" style="left:14px;top:328px;width:150px">Follow up tools help turn a quick question into a booked showing.</p>
  <div class="photo" role="img" aria-label="Photo of a family sitting on a lawn" style="left:172px;top:302px;width:162px;height:110px;background:linear-gradient(180deg,#cfe0c0,#7aa55a)"></div>
  <svg class="swoosh" viewBox="0 0 348 90" height="90" preserveAspectRatio="none" aria-hidden="true">
    <path d="M0 55 Q170 20 348 40 L348 90 L0 90 Z" fill="#cfe0f3"/>
    <path d="M0 70 Q180 38 348 55 L348 90 L0 90 Z" fill="#1756a6"/>
    <path d="M0 80 Q190 55 348 68 L348 90 L0 90 Z" fill="#0d3a78"/>
  </svg>
  <div class="brand" style="right:14px;top:488px"><span class="brand-dot"></span>Harborline Property Partners</div>
</section>

<section class="flier roi">
  <div class="flier-header" style="height:40px"><h2 class="flier-title" style="top:9px;font-size:18px">Return on Investment</h2></div>
  <div role="img" aria-label="Illustration of a rising bar chart and pie chart with a pen"
       style="position:absolute;left:8px;top:48px;width:196px;height:230px;background:radial-gradient(circle at 45% 60%,#e9f0f8,#b9cde3 55%,#ffffff 80%)"></div>
  <div class="tag" style="left:214px;top:110px">Technique 1</div>
  <p class="copy" style="left:214px;top:132px;width:154px">Low monthly cost and more qualified leads mean a faster return on every listing.</p>
  <div class="tag" style="left:214px;top:196px">Technique 2</div>
  <p class="copy" style="left:214px;top:218px;width:154px">Track results by property and spend marketing dollars where they work best.</p>
  <svg class="swoosh" viewBox="0 0 380 60" height="60" preserveAspectRatio="none" aria-hidden="true">
    <path d="M0 30 Q190 5 380 28 L380 60 L0 60 Z" fill="#cfe0f3"/>
    <path d="M0 42 Q200 18 380 40 L380 60 L0 60 Z" fill="#1756a6"/>
    <path d="M0 52 Q200 32 380 50 L380 60 L0 60 Z" fill="#0d3a78"/>
  </svg>
  <div class="brand" style="left:14px;top:290px"><span class="brand-dot"></span>Harborline Property Partners</div>
</section>

<section class="flier broker">
  <div role="img" aria-label="Photo of two business people shaking hands"
       style="position:absolute;left:0;top:0;width:100%;height:175px;background:linear-gradient(160deg,#e6eef7,#a8bfd8 45%,#c79b7a 70%,#3b4a5c)"></div>
  <div class="flier-header" style="height:40px"><h2 class="flier-title" style="top:9px;font-size:18px">Broker Affiliate Program</h2></div>
  <svg style="position:absolute;left:0;top:140px;width:100%;height:40px" viewBox="0 0 380 40" preserveAspectRatio="none" aria-hidden="true">
    <path d="M0 30 Q190 0 380 22 L380 40 L0 40 Z" fill="#cfe0f3"/>
    <path d="M0 36 Q200 12 380 30 L380 40 L0 40 Z" fill="#1756a6"/>
  </svg>
  <div class="broker-panel" style="top:178px;height:157px"></div>
  <p class="broker-head" style="left:14px;top:196px">Technique 1</p>
  <p class="copy light" style="left:14px;top:214px;width:165px">Brokers offer the service to every agent in the office under one simple plan.</p>
  <p class="broker-head" style="left:200px;top:196px">Technique 2</p>
  <p class="copy light" style="left:200px;top:214px;width:165px">Affiliates earn a share of each account and give their team a real edge.</p>
  <div class="brand on-dark" style="right:14px;top:304px"><span class="brand-dot"></span>Harborline Property Partners</div>
</section>

</body>
</html>
```